Book Cover for Harbor Holiday Voyage Needed!

Marble Finch Press needs a cover for a novella. We will need an ebook cover and print wrap. We need to stay with the brand we have as indicated by the files attached. Take a look for the brand and style we are looking for.
Here are the specifics:
Title (subject to change): Seaside Wish
Subtitle: A Christmas Novella
Series Name: The Lagoon Pages Love Series (Book 3.5)
Author: Mira Calloway

Target Market(s)

Romance readers

Industry/Entity Type

Entertainment Industry

Font styles to use
Other font styles liked:
• NovitoNova - Title, Neumann - Subtitle

Colors
3276b5
33a6d7
33b8a4
abd036
fbee3d
ffc214

Requirements
Must have
• Please take a look at the other three covers to stay on brand and for inspiration
Nice to have
• Possibly something with a criuse ship.
Should not have
• Not looking for "real" images or depictions. We want a scene with bright colors same as the previous books but with a bit of a casual feel.

```html
<!DOCTYPE html>
<html lang="en">
<head>
<meta charset="utf-8">
<title>Seaside Wish – Mira Calloway</title>
<link href="https://fonts.googleapis.com/css2?family=Advent+Pro:wght@200;300&family=Dancing+Script:wght@500&family=Gilda+Display&family=Oranienbaum&display=swap" rel="stylesheet">
<style>
  :root {
    --sky-top: #5fa8e0;
    --sky-low: #b9dcf2;
    --sea-deep: #1b8fb8;
    --sea-turquoise: #33b8a4;
    --foam: #f4fbfc;
    --title-white: #ffffff;
    --title-shade: #3a4fa8;
    --series-red: #8a1c1c;
    --author-navy: #2e3f8e;
    --ribbon: #fffdf6;
    --ribbon-edge: #d8b760;
  }
  html, body {
    margin: 0;
    padding: 0;
    overflow: hidden;
    background: #ffffff;
  }
  .cover {
    position: relative;
    width: 751px;
    height: 1200px;
    overflow: hidden;
  }
  .cover-scene {
    position: absolute;
    inset: 0;
    background: linear-gradient(to bottom,
      var(--sky-top) 0%,
      var(--sky-low) 40%,
      var(--sea-deep) 46%,
      #27a6c4 62%,
      var(--sea-turquoise) 76%,
      #bfe6e6 88%,
      var(--foam) 96%);
  }
  .series-ribbon {
    position: absolute;
    left: 108px;
    top: 78px;
    width: 520px;
    height: 74px;
  }
  .series-name {
    position: absolute;
    left: 0;
    width: 751px;
    top: 98px;
    text-align: center;
    font-family: "Gilda Display", serif;
    font-size: 25px;
    color: var(--series-red);
    letter-spacing: 0.2px;
    margin: 0;
  }
  .title-art {
    position: absolute;
    left: 0;
    top: 0;
    width: 751px;
    height: 800px;
  }
  .title-line {
    font-family: "Advent Pro", sans-serif;
    font-weight: 200;
  }
  .title-shade { fill: var(--title-shade); }
  .title-face { fill: var(--title-white); }
  .subtitle {
    position: absolute;
    left: 0;
    width: 751px;
    top: 712px;
    margin: 0;
    text-align: center;
    font-family: "Dancing Script", cursive;
    font-weight: 500;
    font-size: 44px;
    color: var(--title-white);
    text-shadow: 2px 2px 0 var(--title-shade);
  }
  .author {
    position: absolute;
    left: 0;
    width: 751px;
    top: 1068px;
    margin: 0;
    text-align: center;
    font-family: "Oranienbaum", serif;
    font-weight: 400;
    font-size: 62px;
    letter-spacing: 2px;
    color: var(--author-navy);
  }
</style>
</head>
<body>
<main class="cover">
  <div class="cover-scene" role="img" aria-label="Tropical beach scene: palm tree against a bright blue sky, a cruise ship on turquoise sea and a breaking wave in the foreground"></div>

  <svg class="series-ribbon" viewBox="0 0 520 74" aria-hidden="true">
    <path d="M4 22 Q260 0 516 18 L500 52 Q260 66 20 60 Z" fill="var(--ribbon)" stroke="var(--ribbon-edge)" stroke-width="2"/>
  </svg>
  <p class="series-name">Lagoon Pages Love Series (Book 3.5)</p>

  <svg class="title-art" viewBox="0 0 751 800" role="img" aria-label="Seaside Wish">
    <g class="title-line">
      <text class="title-shade" x="126" y="380" font-size="206" textLength="512" lengthAdjust="spacingAndGlyphs">SEASIDE</text>
      <text class="title-face" x="120" y="376" font-size="206" textLength="512" lengthAdjust="spacingAndGlyphs">SEASIDE</text>
      <text class="title-shade" x="127" y="692" font-size="424" textLength="512" lengthAdjust="spacingAndGlyphs">WISH</text>
      <text class="title-face" x="120" y="688" font-size="424" textLength="512" lengthAdjust="spacingAndGlyphs">WISH</text>
    </g>
  </svg>

  <p class="subtitle">A Christmas Novella</p>
  <h2 class="author">MIRA CALLOWAY</h2>
</main>
</body>
</html>
```